University Student Business Card

Looking for a professional university student business card. Student is studying business with a focus on marketing. Some combination using a monogram and/or full name on the front with full name, university details and contact information on the back. Card should be modern design for a young professional. Prefer use of royal blue, black and white but am open to other uses of colour palette if it reinforces young/trendy style. Initials for a monogram are: KR. Full details will be provided in private consultation with designer(s).

Target Market(s)

Professional business people, marketers, advertisers, consultants

Industry/Entity Type

Business, marketing

Contact Information for Business Card

Monogram or personal logo, full name, university name, program of study, phone number, email address, pathfolio address

Other font styles liked:
• Open to suggestion to fulfill above requirements

Colors
0054AA
0677BA
7BADD7
CADEEF
E8F1F8

Requirements
Must have
• Monogram using letters K and R, and incorporate the business card details listed in the brief (specific details including personal contact info will be shared with successful designer to ensure privacy)
Nice to have
• Personal brand using monogram or personal logo (not a business logo)

```html
<!DOCTYPE html>
<html lang="en">
<head>
<meta charset="utf-8">
<title>KR Student Business Card</title>
<link rel="stylesheet" href="https://fonts.googleapis.com/css2?family=Lato:wght@400;700&family=Arimo:wght@400&display=swap">
<style>
  :root {
    --bg: #2a2a2b;
    --card: #1c1d1f;
    --card-deep: #151618;
    --blue: #0054aa;
    --blue-light: #0677ba;
    --grey-text: #a7a9ac;
    --rule: #6d6f72;
    --white: #ffffff;
  }
  * { margin: 0; padding: 0; box-sizing: border-box; }
  html, body { width: 1200px; height: 1108px; overflow: hidden; background: var(--bg); }
  .stage {
    width: 1200px; height: 1108px;
    display: flex; align-items: center; justify-content: center; gap: 70px;
  }
  .card {
    position: relative;
    width: 400px; height: 680px;
    background: var(--card);
    border-radius: 26px;
    overflow: hidden;
    box-shadow: 0 18px 40px rgba(0,0,0,.45);
    font-family: "Arimo", Arial, sans-serif;
    text-align: center;
  }
  /* front */
  .monogram-large {
    position: absolute; top: 110px; left: 0; right: 0;
    font-family: "Lato", sans-serif; font-weight: 700;
    font-size: 190px; line-height: 1; letter-spacing: 4px;
    color: var(--blue);
  }
  .university-name {
    position: absolute; top: 356px; left: 0; right: 0;
    font-family: "Lato", sans-serif; font-weight: 400;
    font-size: 30px; letter-spacing: 1px; color: var(--blue);
  }
  .rule { display: block; height: 1px; background: var(--rule); margin: 0 auto; }
  .front .rule-top { position: absolute; top: 410px; left: 90px; width: 220px; }
  .address {
    position: absolute; top: 428px; left: 0; right: 0;
    font-size: 20px; line-height: 26px; color: var(--grey-text);
  }
  .icon-row {
    position: absolute; top: 502px; left: 40px; right: 40px;
    display: flex; align-items: center; gap: 10px;
  }
  .icon-row .rule { flex: 1; }
  .icon-box {
    width: 34px; height: 34px; border-radius: 5px;
    background: var(--blue); display: flex; align-items: center; justify-content: center;
  }
  .contact {
    position: absolute; top: 560px; left: 0; right: 0;
    font-size: 21px; line-height: 28px; color: var(--grey-text);
  }
  /* back */
  .monogram-pattern {
    position: absolute; inset: 0;
    background: linear-gradient(160deg, #2e2f32 0%, #1e1f21 45%, var(--card-deep) 100%);
  }
  .back-content { position: absolute; top: 392px; left: 0; right: 0; }
  .monogram-small {
    font-family: "Lato", sans-serif; font-weight: 700;
    font-size: 56px; line-height: 1; letter-spacing: 2px; color: var(--blue);
  }
  .person-name {
    margin-top: 34px;
    font-family: "Lato", sans-serif; font-size: 34px; letter-spacing: 1px;
    color: var(--blue);
  }
  .programme { margin-top: 4px; font-size: 21px; color: var(--white); }
  .back .rule { width: 120px; margin-top: 18px; }
  .profile-link {
    margin-top: 22px; display: flex; align-items: center; justify-content: center; gap: 12px;
    font-size: 22px; color: var(--white);
  }
  .profile-dot { width: 34px; height: 34px; border-radius: 50%; background: var(--blue-light); }
</style>
</head>
<body>
<main class="stage">
  <section class="card front" aria-label="Card front">
    <div class="monogram-large">KR</div>
    <h1 class="university-name">UNIVERSITY NAME</h1>
    <span class="rule rule-top"></span>
    <p class="address">421, Address line here<br>45452, Country Name</p>
    <div class="icon-row">
      <span class="rule"></span>
      <span class="icon-box" aria-label="Phone">
        <svg width="20" height="20" viewBox="0 0 24 24"><path fill="#1c1d1f" d="M6.6 10.8a15 15 0 0 0 6.6 6.6l2.2-2.2c.3-.3.7-.4 1-.2 1.1.4 2.3.6 3.6.6.6 0 1 .4 1 1V20c0 .6-.4 1-1 1A17 17 0 0 1 3 4c0-.6.4-1 1-1h3.5c.6 0 1 .4 1 1 0 1.3.2 2.5.6 3.6.1.3 0 .7-.2 1z"/></svg>
      </span>
      <span class="icon-box" aria-label="Email">
        <svg width="20" height="20" viewBox="0 0 24 24"><rect x="2" y="5" width="20" height="14" fill="#1c1d1f"/><path d="M2 5l10 8 10-8M2 19l7-7M22 19l-7-7" stroke="#0054aa" stroke-width="1.6" fill="none"/></svg>
      </span>
      <span class="icon-box" aria-label="Website">
        <svg width="20" height="20" viewBox="0 0 24 24"><circle cx="12" cy="12" r="9" fill="#1c1d1f"/><path d="M3 12h18M12 3c3 3 3 15 0 18M12 3c-3 3-3 15 0 18" stroke="#0054aa" stroke-width="1.4" fill="none"/></svg>
      </span>
      <span class="rule"></span>
    </div>
    <p class="contact">055-321 654 987<br>hello@kremail.com<br>www.krstudio.com</p>
  </section>

  <section class="card back" aria-label="Card back">
    <div class="monogram-pattern" role="img" aria-label="Faint repeating monogram pattern in dark glossy tones"></div>
    <div class="back-content">
      <div class="monogram-small">KR</div>
      <h2 class="person-name">JORDAN ELLIS</h2>
      <p class="programme">Business Marketing</p>
      <span class="rule"></span>
      <p class="profile-link"><span class="profile-dot"></span>pathfolio.com/name</p>
    </div>
  </section>
</main>
</body>
</html>
```